Design a great website for our amazing new country club in Southern California!

Our old neighborhood golf club is being transformed into a 100% new world-class club located down the street from the old location. We want a new website look that projects our new image. However because the club hasn't been built yet, we don't have a lot of images--just a new logo and a few renderings. So we will add images in the coming months as things get built. In the meantime, for things such as restaurant or swimming or tennis pics, feel free to plug in stock internet images for now. And regarding the movie file, we had an idea for a dramatic headline slowly rising over the clubhouse. It's just an idea, however, we're not married to it. We need to get creative here, as we have so few images. Oh, and we definitely want one main graphic on the home page. We don't like the slide-show effect--looks cheap. And finally, the landing page will be a 'public' page with other pages aimed at attracting new members. There will also be a 'Members area' that is password-protected. Site maps and rough copy for each of the two sections is included. Good luck!! :-) Please view our current website: quillbrookcc.com

Target Market(s)

Wealthy folks who like golf, sports and dining. Our memberships range in price from $18,000 to $130,000.

Industry/Entity Type

Club

Coding

Coded - Design and coding required

Number of Pages Required

5+ page

Font styles to use
Sans Serif

Requirements
Must have
• a GORGEOUS home page, with buttons and features that will remain static on all other pages. We want the navigation buttons along the top with pull-downs. Only the areas below the nav buttons will change. We want this site to look very clean and classy.
Nice to have
• Maybe have the button 'glow' or enlarge or whatever when you roll over them. Whatever can spruce up the simple classy design. Maybe so some special effect to the QB logo as well. As long as it looks classy, that's the main thing. And if you can find some good generic images of golf, dining, swimming, tennis, whatever on the net, feel free to use them.
Should not have
• No slide show effects, with multiple images changing.

```html
<!DOCTYPE html>
<html lang="en">
<head>
<meta charset="utf-8">
<title>Quillbrook Country Club</title>
<link rel="stylesheet" href="https://fonts.googleapis.com/css2?family=Cinzel:wght@400;600;700&family=Open+Sans:wght@400;600;700&display=swap">
<style>
:root{
  --ink:#1b1b1b;
  --white:#ffffff;
  --grey-text:#6f6f6f;
  --dark-panel:#262626;
  --footer:#1f1f1f;
  --footer-text:#9a9a9a;
  --footer-name:#5a5a5a;
  --bar:rgba(0,0,0,.72);
  --play:#e0463f;
  --serif:'Cinzel', serif;
  --sans:'Open Sans', sans-serif;
}
*{margin:0;padding:0;box-sizing:border-box}
html,body{width:1200px;height:3742px;overflow:hidden}
body{font-family:var(--sans);color:var(--ink);background:var(--white);position:relative}
section,header,footer{position:absolute;left:0;width:1200px;overflow:hidden}
.photo{position:absolute;inset:0}
.btn{display:inline-block;border:2px solid var(--white);color:var(--white);font-family:var(--serif);font-size:15px;letter-spacing:1px;padding:10px 28px;text-decoration:none}

/* Hero */
.hero{top:0;height:641px}
.hero .photo{background:linear-gradient(180deg,#1d2733 0%,#3d4b55 35%,#4f6a78 55%,#5f7f88 72%,#3c4a3a 100%)}
.hero .photo::after{content:"";position:absolute;inset:0;background:radial-gradient(ellipse 420px 180px at 600px 520px,rgba(120,190,220,.45),transparent)}
.site-nav{position:absolute;top:0;left:0;width:1200px;height:150px}
.brand{position:absolute;left:42px;top:52px;width:160px;text-align:center;color:var(--white);font-family:var(--sans);font-weight:600;font-size:13px;line-height:1.5;letter-spacing:1.5px;text-transform:uppercase}
.nav-links{list-style:none}
.nav-links li{position:absolute;top:68px;font-size:12px;color:var(--white);text-transform:uppercase;letter-spacing:.3px;white-space:nowrap}
.nav-links li:nth-child(1){left:474px}
.nav-links li:nth-child(2){left:599px}
.nav-links li:nth-child(3){left:731px}
.nav-links li:nth-child(4){left:818px}
.nav-links li:nth-child(5){left:1025px}
.hero-center{position:absolute;top:195px;left:0;width:1200px;text-align:center;color:var(--white)}
.hero-name{height:165px;display:flex;align-items:center;justify-content:center;font-family:var(--sans);font-weight:600;font-size:54px;letter-spacing:10px;text-transform:uppercase}
.hero-title{font-family:var(--serif);font-size:33px;letter-spacing:1px;margin-top:14px}
.hero-center .btn{margin-top:22px}

/* Intro */
.intro{top:641px;height:499px;background:var(--white)}
.intro .photo{background:linear-gradient(180deg,#f4f5f2 0%,#e9ece6 45%,#f7f7f5 80%,#ffffff 100%);opacity:.9}
.intro-body{position:absolute;top:150px;left:0;width:1200px;text-align:center}
.intro-title{font-family:var(--serif);font-size:62px;font-weight:600;line-height:1}
.intro-sub{font-family:var(--serif);font-size:26px;letter-spacing:7px;margin-top:14px}
.intro-text{width:920px;margin:30px auto 0;font-size:12px;line-height:2;color:var(--grey-text)}

/* Membership */
.membership{top:1140px;height:437px}
.membership .photo{background:linear-gradient(110deg,#3a2a22 0%,#6b4c3c 30%,#4a3a30 55%,#6e5443 80%,#2d231d 100%)}
.membership .photo::after{content:"";position:absolute;inset:0;background:rgba(0,0,0,.35)}
.membership-body{position:absolute;top:112px;width:1200px;text-align:center;color:var(--white)}
.section-title{font-family:var(--serif);font-size:52px;font-weight:600;letter-spacing:2px;line-height:1}
.membership-body p{width:880px;margin:26px auto 0;font-size:12px;line-height:2}
.membership-body .btn{margin-top:26px}

/* Programs */
.programs{top:1577px;height:955px;background:var(--white)}
.programs .section-title{position:absolute;top:78px;width:1200px;text-align:center;color:var(--ink)}
.programs-lead{position:absolute;top:148px;width:1200px;text-align:center;font-size:12px;color:var(--grey-text)}
.program-grid{position:absolute;top:209px;left:100px;width:1003px;display:grid;grid-template-columns:repeat(3,1fr);gap:2px}
.tile{position:relative;height:333px;overflow:hidden}
.tile-bar{position:absolute;left:0;right:0;bottom:0;height:98px;background:var(--bar);text-align:center;color:var(--white);padding-top:18px}
.tile-name{font-family:var(--serif);font-size:26px;letter-spacing:1px}
.tile-link{font-size:10px;font-weight:700;margin-top:4px;text-transform:uppercase}
.tile-dining{background:#1e1e1e;color:var(--white);padding:66px 42px 0 48px}
.tile-dining .tile-name{font-size:28px}
.tile-dining p{font-size:11.5px;line-height:1.9;margin-top:14px}
.tile-dining .tile-link{margin-top:28px}
.fitness{background:linear-gradient(160deg,#d8dce0,#b48a72 45%,#e7e2dc)}
.aquatics{background:linear-gradient(150deg,#0f2d35,#2f7d90 40%,#d19a3a 75%,#6a4a2a)}
.tennis{background:linear-gradient(180deg,#cfd6db,#9aa3a6 60%,#5c6c5c)}
.spa{background:linear-gradient(150deg,#e9cfb7,#c48f70 50%,#7a4a35)}
.wine{background:linear-gradient(160deg,#3d2b22,#7a2a28 45%,#2a1a14)}

/* How it works */
.how{top:2532px;height:432px}
.how-media{position:absolute;left:0;top:0;width:599px;height:432px;background:linear-gradient(180deg,#9cb7cf 0%,#c9d6df 40%,#8d7b66 62%,#5f7048 100%)}
.play{position:absolute;left:254px;top:168px}
.how-panel{position:absolute;left:599px;top:0;width:601px;height:432px;background:var(--dark-panel);color:var(--white);padding:110px 80px 0 92px}
.how-panel .section-title{font-size:48px;letter-spacing:1px}
.how-panel p{font-size:12px;line-height:2;margin-top:22px}
.how-panel .btn{margin-top:26px}

/* Testimonial */
.testimonial{top:2964px;height:387px}
.testimonial .photo{background:linear-gradient(90deg,#3a3e33 0%,#5b6252 30%,#41483c 55%,#6a6a55 80%,#2f332b 100%)}
.testimonial .photo::after{content:"";position:absolute;inset:0;background:rgba(0,0,0,.45)}
.testimonial-body{position:absolute;top:86px;width:1200px;text-align:center;color:var(--white)}
.testimonial-body blockquote{width:880px;margin:22px auto 0;font-size:12px;line-height:2.1}
.avatar{width:92px;height:92px;border-radius:50%;border:3px solid var(--white);background:linear-gradient(180deg,#c9d3dc,#8a99a8);margin:32px auto 0}
.cite{margin-top:14px;font-size:12px}
.cite strong{font-weight:700}

/* Footer */
.site-footer{top:3351px;height:391px;background:var(--footer);text-align:center;color:var(--footer-text)}
.footer-name{height:78px;margin-top:42px;display:flex;align-items:center;justify-content:center;font-family:var(--sans);font-weight:600;font-size:26px;letter-spacing:6px;text-transform:uppercase;color:var(--footer-name)}
.contact{display:flex;justify-content:center;gap:34px;margin-top:58px;font-size:11.5px;color:#cfcfcf}
.contact span{display:flex;align-items:center;gap:8px}
.footer-links{display:flex;justify-content:center;gap:34px;margin-top:18px;font-size:11.5px;color:#cfcfcf}
.copyright{margin-top:16px;font-size:11.5px;color:#cfcfcf}
.social{display:flex;justify-content:center;gap:8px;margin-top:28px}
.social span{width:24px;height:24px;border-radius:50%;background:#5a5a5a}
</style>
</head>
<body>

<header class="hero">
  <div class="photo" role="img" aria-label="Aerial rendering of the clubhouse pool deck with cabanas and umbrellas"></div>
  <nav class="site-nav">
    <div class="brand">Quillbrook<br>Country Club</div>
    <ul class="nav-links">
      <li>Guest Info</li>
      <li>Membership</li>
      <li>Golf</li>
      <li>Club House &amp; Amenities</li>
      <li>Wedding &amp; Events</li>
    </ul>
  </nav>
  <div class="hero-center">
    <div class="hero-name">Quillbrook</div>
    <div class="hero-title">Quillbrook Country Club's</div>
    <a class="btn" href="#">Join us now</a>
  </div>
</header>

<section class="intro">
  <div class="photo" role="img" aria-label="Faint pencil sketch of the clubhouse"></div>
  <div class="intro-body">
    <h1 class="intro-title">Quillbrook</h1>
    <div class="intro-sub">COUNTRY CLUB</div>
    <p class="intro-text">Established in 1965, Quillbrook Country Club has remained true to founder Walter J. Penrose's vision of the only family-oriented private club within the South Bay. The character and camaraderie of the individuals who comprise the Club's membership are among its most outstanding attributes. Quillbrook Country Club is a home away from home for friends and generations of families, where they come together to celebrate some of life's most cherished events. From birthdays to wedding days, Quillbrook provides the perfect venue for any event and memories that will last a lifetime.</p>
  </div>
</section>

<section class="membership">
  <div class="photo" role="img" aria-label="Friends laughing together outdoors in the sun"></div>
  <div class="membership-body">
    <h2 class="section-title">MEMBERSHIP</h2>
    <p>Lorem Ipsum is simply dummy text of the printing and typesetting industry. Lorem Ipsum has been the industry's standard dummy text ever since the 1500s, when an unknown printer took a galley of type and scrambled it to make a type specimen book. It has survived not only five centuries, but also the leap into electronic typesetting...</p>
    <a class="btn" href="#">Join us now</a>
  </div>
</section>

<section class="programs">
  <h2 class="section-title">Programs</h2>
  <p class="programs-lead">Lorem Ipsum is simply dummy text of the printing and typesetting industry. Lorem Ipsum has been the industry's standard dummy</p>
  <div class="program-grid">
    <article class="tile tile-dining">
      <div class="tile-name">DINING</div>
      <p>QBCC will offer multiple dining options featuring spectacular panoramic views of the Los Angeles basin plus seven holes of the golf course. There will be no finer place in the South Bay to enjoy a great meal and while-away the day or evening.</p>
      <div class="tile-link">Click here for view info »</div>
    </article>
    <article class="tile">
      <div class="photo fitness" role="img" aria-label="Runners training in a fitness studio"></div>
      <div class="tile-bar"><div class="tile-name">FITNESS</div><div class="tile-link">Click here for view info »</div></div>
    </article>
    <article class="tile">
      <div class="photo aquatics" role="img" aria-label="Tropical fish in blue water"></div>
      <div class="tile-bar"><div class="tile-name">AQUATICS</div><div class="tile-link">Click here for view info »</div></div>
    </article>
    <article class="tile">
      <div class="photo tennis" role="img" aria-label="Tennis players on a court"></div>
      <div class="tile-bar"><div class="tile-name">TENNIS</div><div class="tile-link">Click here for view info »</div></div>
    </article>
    <article class="tile">
      <div class="photo spa" role="img" aria-label="Guests relaxing at a spa"></div>
      <div class="tile-bar"><div class="tile-name">SPA</div><div class="tile-link">Click here for view info »</div></div>
    </article>
    <article class="tile">
      <div class="photo wine" role="img" aria-label="Wine bottles resting in a cellar rack"></div>
      <div class="tile-bar"><div class="tile-name">WINE ROOM</div><div class="tile-link">Click here for view info »</div></div>
    </article>
  </div>
</section>

<section class="how">
  <div class="how-media" role="img" aria-label="Rendering of the clubhouse terrace and gardens, video preview"></div>
  <svg class="play" width="92" height="92" viewBox="0 0 92 92" aria-hidden="true">
    <circle cx="46" cy="46" r="46" fill="var(--play)"/>
    <path d="M37 28 L65 46 L37 64 Z" fill="#ffffff"/>
  </svg>
  <div class="how-panel">
    <h2 class="section-title">How it works?</h2>
    <p>Lorem Ipsum is simply dummy text of the printing and typesetting industry. Lorem Ipsum has been the industry's standard dummy text ever since the 1500s, when an unknown printer took a galley of type and scrambled it to make a type specimen book. It has survived not only five centuries...</p>
    <a class="btn" href="#">Join us now</a>
  </div>
</section>

<section class="testimonial">
  <div class="photo" role="img" aria-label="Two golfers on the course seen from behind"></div>
  <div class="testimonial-body">
    <svg width="30" height="24" viewBox="0 0 30 24" aria-hidden="true">
      <path d="M0 24V13C0 5 4 1 12 0v5c-4 1-6 3-6 7h6v12Z M17 24V13c0-8 4-12 12-13v5c-4 1-6 3-6 7h6v12Z" fill="#cfcfcf"/>
    </svg>
    <blockquote>Lorem Ipsum is simply dummy text of the printing and typesetting industry. Lorem Ipsum has been the industry's standard dummy text ever since the 1500s, when an unknown printer took a galley of type and scrambled it to make a type specimen book</blockquote>
    <div class="avatar" role="img" aria-label="Portrait of the member"></div>
    <div class="cite"><strong>- Miles Harmon</strong> - Business man</div>
  </div>
</section>

<footer class="site-footer">
  <div class="footer-name">Quillbrook</div>
  <div class="contact">
    <span><svg width="12" height="12" viewBox="0 0 12 12" aria-hidden="true"><path d="M2 1h3l1 3-2 1c1 2 2 3 4 4l1-2 3 1v3c-6 0-10-4-10-10Z" fill="#cfcfcf"/></svg>(310) 555-0142</span>
    <span><svg width="13" height="10" viewBox="0 0 13 10" aria-hidden="true"><rect x=".5" y=".5" width="12" height="9" fill="none" stroke="#cfcfcf"/><path d="M.5 .5 6.5 5.5 12.5 .5" fill="none" stroke="#cfcfcf"/></svg>members@quillbrookcc.com</span>
    <span><svg width="12" height="12" viewBox="0 0 12 12" aria-hidden="true"><circle cx="6" cy="6" r="5.3" fill="none" stroke="#cfcfcf" stroke-width="1.2"/><path d="M6 3v3.3h2.5" fill="none" stroke="#cfcfcf" stroke-width="1.2"/></svg>Mon - Fri : 9.00am to 6.00pm, Sunday : leave</span>
  </div>
  <div class="footer-links">
    <span>Guest Info</span><span>Membership</span><span>Golf</span><span>Club House &amp; Amenities</span><span>Wedding &amp; Events</span>
  </div>
  <div class="copyright">© Copyrights 2016. Quillbrook Country Club. All rights reserved.</div>
  <div class="social" aria-label="Social links">
    <span></span><span></span><span></span><span></span><span></span>
  </div>
</footer>

</body>
</html>
```